Redesign of business card for Cedar Ridge Mechanical

We are looking for a new design for our business cards for Cedar Ridge Mechanical. We are a plumbing & HVAC construction company, operating on the West Coast of Canada and USA. Logo attached.
Industry/Entity Type
Construction - Plumbing & HVAC
Contact Information for Business Card
Name, address, phone numbers, email, website address
Look and feel
Each slider illustrates characteristics of the customer's brand and the style your logo design should communicate.

```html
<!DOCTYPE html>
<html lang="en">
<head>
<meta charset="utf-8">
<title>Cedar Ridge Mechanical – Business Card</title>
<link href="https://fonts.googleapis.com/css2?family=Montserrat:wght@400;600;700&display=swap" rel="stylesheet">
<style>
  :root {
    --stage: #2e2e30;
    --ink: #141414;
    --card-black: #1a1a1a;
    --paper: #ffffff;
    --stripe-grey: #9a9a9a;
    --text-light: #f2f2f2;
    --text-muted: #d0d0d0;
    --back-mark: #2a2a2a;
  }
  * { margin: 0; padding: 0; box-sizing: border-box; }
  html, body { width: 1200px; height: 913px; overflow: hidden; background: var(--stage); }
  .stage { position: relative; width: 1200px; height: 913px; font-family: "Montserrat", sans-serif; }

  .card {
    position: absolute;
    width: 620px; height: 354px;
    border-radius: 22px;
    overflow: hidden;
  }

  /* Back of card */
  .card-back { left: 90px; top: 70px; background: var(--card-black); }
  .card-back .brand-name {
    position: absolute; inset: 0;
    display: flex; align-items: center; justify-content: center; gap: 18px;
    color: var(--back-mark);
    font-weight: 700; font-size: 32px; letter-spacing: 2px; text-transform: uppercase;
  }
  .card-back .brand-square { width: 40px; height: 40px; border: 5px solid var(--back-mark); flex: none; }

  /* Front of card */
  .card-front { left: 490px; top: 480px; background: var(--paper); }
  .card-front .wave { position: absolute; inset: 0; }
  .card-front .brand {
    position: absolute; right: 34px; top: 40px;
    display: flex; align-items: center; gap: 12px;
    color: var(--ink); font-weight: 700; font-size: 21px; letter-spacing: 1px; text-transform: uppercase;
  }
  .card-front .brand-square { width: 26px; height: 26px; border: 4px solid var(--ink); flex: none; }

  .person { position: absolute; left: 40px; top: 196px; color: var(--text-light); }
  .person .name { font-weight: 700; font-size: 24px; letter-spacing: 0.5px; line-height: 30px; }
  .person .role { font-weight: 400; font-size: 15px; color: var(--text-muted); margin-top: 2px; }

  .contacts { position: absolute; left: 40px; top: 266px; list-style: none; color: var(--text-light); font-size: 16px; }
  .contacts li { display: flex; align-items: center; gap: 9px; line-height: 24px; }
  .contacts svg { width: 14px; height: 14px; fill: var(--text-light); }

  .address {
    position: absolute; right: 34px; top: 165px;
    text-align: right; color: var(--text-light); font-size: 15px; line-height: 22px; font-style: normal;
  }
</style>
</head>
<body>
<main class="stage">

  <section class="card card-back" aria-label="Business card back">
    <div class="brand-name"><span class="brand-square"></span>Cedar Ridge Mechanical</div>
  </section>

  <section class="card card-front" aria-label="Business card front">
    <svg class="wave" viewBox="0 0 620 354" preserveAspectRatio="none" aria-hidden="true">
      <path d="M0,354 L0,180 C90,140 190,150 300,128 C420,104 520,100 620,95 L620,354 Z" fill="var(--card-black)"/>
      <path d="M250,138 C330,118 430,90 620,80 L620,95 C520,100 420,104 300,128 C285,131 268,135 250,138 Z" fill="var(--stripe-grey)"/>
      <path d="M0,166 C60,140 120,130 175,132 C120,138 60,152 0,174 Z" fill="var(--card-black)"/>
    </svg>

    <div class="brand"><span class="brand-square"></span>Cedar Ridge Mechanical</div>

    <address class="address">Your address, City<br>State, Zip 1234</address>

    <div class="person">
      <div class="name">DANIEL HART</div>
      <div class="role">Managing Director</div>
    </div>

    <ul class="contacts">
      <li><svg viewBox="0 0 16 16"><path d="M3 1l3 3-2 2c1 2 3 4 5 5l2-2 3 3-2 3C7 15 1 9 1 3z"/></svg>123 456 789</li>
      <li><svg viewBox="0 0 16 16"><path d="M1 3h14v10H1z M2 4l6 5 6-5" fill="none" stroke="#f2f2f2" stroke-width="1.6"/></svg>info@cedarridgemech.com</li>
      <li><svg viewBox="0 0 16 16"><circle cx="8" cy="8" r="6.5" fill="none" stroke="#f2f2f2" stroke-width="1.6"/><path d="M1.5 8h13M8 1.5c-3 3-3 10 0 13M8 1.5c3 3 3 10 0 13" fill="none" stroke="#f2f2f2" stroke-width="1.2"/></svg>www.cedarridgemech.com</li>
    </ul>
  </section>

</main>
</body>
</html>
```